Salon Signage

We need a new company sign designed for the exterior of our salon. I have attached our current logos for an idea. I have also attached a photo of what salon looks like currently.

```html
<!DOCTYPE html>
<html lang="en">
<head>
<meta charset="utf-8">
<title>Glosswave Beauty Salon Sign</title>
<link href="https://fonts.googleapis.com/css2?family=Archivo+Black&family=Dancing+Script:wght@600&family=Montserrat:wght@700&display=swap" rel="stylesheet">
<style>
  :root {
    --bg-light: #f9e6e1;
    --bg-warm: #f4ddd7;
    --ink: #1e1c1a;
    --plum: #a6268a;
    --magenta: #d91b72;
    --white: #ffffff;
    --art-center: #f6d9d2;
    --art-edge: #e6c6c0;
  }
  html, body {
    margin: 0;
    padding: 0;
    width: 1200px;
    height: 301px;
    overflow: hidden;
  }
  .salon-sign {
    display: block;
    width: 1200px;
    height: 301px;
  }
  .brand-name {
    font-family: "Archivo Black", "Arial Black", sans-serif;
  }
  .brand-name-first { fill: var(--ink); }
  .brand-name-second { fill: var(--plum); }
  .tagline {
    font-family: "Dancing Script", cursive;
    font-weight: 600;
    fill: var(--ink);
  }
  .phone-number {
    font-family: "Montserrat", Arial, sans-serif;
    font-weight: 700;
    fill: var(--white);
  }
</style>
</head>
<body>
<svg class="salon-sign" viewBox="0 0 1200 301" xmlns="http://www.w3.org/2000/svg">
  <defs>
    <linearGradient id="sign-background" x1="0" y1="0" x2="1" y2="0">
      <stop offset="0" stop-color="var(--bg-light)"/>
      <stop offset="1" stop-color="var(--bg-warm)"/>
    </linearGradient>
    <linearGradient id="accent-band" x1="0" y1="0" x2="1" y2="0">
      <stop offset="0" stop-color="var(--plum)"/>
      <stop offset="1" stop-color="var(--magenta)"/>
    </linearGradient>
    <radialGradient id="stylist-art" cx="0.5" cy="0.45" r="0.55">
      <stop offset="0" stop-color="var(--art-center)"/>
      <stop offset="1" stop-color="var(--art-edge)"/>
    </radialGradient>
  </defs>

  <rect class="background" width="1200" height="301" fill="url(#sign-background)"/>

  <circle class="stylist-illustration" cx="191" cy="152" r="135" fill="url(#stylist-art)"
          role="img" aria-label="Illustration of a hair stylist holding salon tools: hair dryer, brushes, scissors, straightener and colour swatches"/>

  <text class="brand-name" x="374" y="150" font-size="152" textLength="790" lengthAdjust="spacingAndGlyphs"><tspan class="brand-name-first">GLOSS</tspan><tspan class="brand-name-second">WAVE</tspan></text>

  <text class="tagline" x="364" y="232" font-size="96" textLength="405" lengthAdjust="spacingAndGlyphs">Beauty Salon</text>

  <polygon class="phone-band" points="787,229 1200,229 1200,291 755,291" fill="url(#accent-band)"/>
  <text class="phone-number" x="794" y="279" font-size="47" textLength="380" lengthAdjust="spacingAndGlyphs">(03) 5550 1427</text>

  <rect class="base-stripe" x="0" y="291" width="1200" height="10" fill="url(#accent-band)"/>
</svg>
</body>
</html>
```